Business Card - high end, modern health care

Hey designers!

We need a double sided business card for the boutique, cutting edge physical therapy rehabilitation centre in Sydney's Northern Beaches.

With the most qualified physios in the area The Harbourview Motion Clinic does what other physiotherapy practices do not, we take our time with our patients giving them longer appointments, better physios and therefor faster results!

We guarantee that the service people receive at THMC will be unparalleled.

Hence we need a business card to reflect our modern, boutique, high end service. The final design needs to reflect that we are in a class of our own yet with the feel of beachside retreat.

Below I have attached our logo in both blue on white and white on blue. The exact colour is;
and the font that we have used in our logo is Tex Gyre Aventador.

I like the idea of the blue as the main colour as it is more eye catching and our signage onto the main road will be in this blue and in the interest of consistency across marketing the blue needs to be a part of the design. However I would appreciate a few designs onto a wooden background as this is a visual theme within the fitout of the practice.

The design needs to be of standard size (91x55mm).

Target Market(s)

We target people who have an end outcome in mind and those who have had poor experiences with other providers and ensure that everyone gets the care that they deserve with a premium service that is tailored to the individuals circumstances. As a premium service, the target market is highly educated, business and tech savvy with the additional target market of elderly people who have self funded their retirement and see value in paying for the best ongoing rehabilitation to maintain independence.

Industry/Entity Type

Physical Therapy

Contact Information for Business Card

Name, designation( Titled Musculoskeletal Physiotherapist... there will also be those in the company that have multiple designations ie 5 or 6 words long), phone number, email, facebook, instagram, address

Font styles to use
Sans Serif

Colors

Designer to choose colors to be used in the design.

Requirements
Must have
• Front - The logo as large as possible, blue or wooden theme, and all of the important details.
• Back - A blank space/lines on which to write appointment times (no "Appointment, date, time" etc.)
Nice to have
• facebook url
• logos for facebook and instagram
• Mini logos for the phone and email?

```html
<!DOCTYPE html>
<html lang="en">
<head>
<meta charset="utf-8">
<title>The Harbourview Motion Clinic – Business Card</title>
<link rel="stylesheet" href="https://fonts.googleapis.com/css2?family=Raleway:wght@300;400;500;700&display=swap">
<style>
  :root {
    --brand-blue: #0d55a5;
    --ink: #1b1b1b;
    --paper: #fbfbfb;
    --page: #e9e9e9;
    --rule: #2a2a2a;
    --dash: #9a9a9a;
    --social-a: #1d8fd6;
    --social-b: #e0458f;
  }
  * { box-sizing: border-box; margin: 0; padding: 0; }
  html, body { width: 1200px; height: 1200px; overflow: hidden; }
  body {
    background: var(--page);
    font-family: "Raleway", sans-serif;
    color: var(--ink);
    display: flex;
    flex-direction: column;
    align-items: center;
    justify-content: center;
    gap: 60px;
  }
  .card {
    position: relative;
    width: 860px;
    height: 520px;
    box-shadow: 0 6px 20px rgba(0,0,0,0.15);
    overflow: hidden;
  }

  /* Brand side */
  .card--brand { background: var(--brand-blue); color: #fff; }
  .brand-disc {
    position: absolute;
    left: 190px; top: 110px;
    width: 300px; height: 300px;
    border-radius: 50%;
    background: #fff;
  }
  .brand-lockup {
    position: absolute;
    left: 520px; top: 300px;
    display: flex; align-items: center; gap: 12px;
  }
  .lockup-dot {
    width: 44px; height: 44px; border-radius: 50%;
    background: currentColor; flex: none;
  }
  .lockup-name {
    font-weight: 700;
    line-height: 1.05;
    text-transform: uppercase;
  }
  .lockup-name .line-1 { display: block; font-size: 22px; letter-spacing: 0.02em; }
  .lockup-name .line-2 { display: block; font-size: 15px; letter-spacing: 0.32em; }

  /* Detail side */
  .card--details { background: var(--paper); }
  .person {
    position: absolute; left: 90px; top: 70px;
  }
  .person-name {
    font-weight: 300; font-size: 42px; letter-spacing: 0.01em;
  }
  .person-name .accent { color: var(--brand-blue); }
  .person-role { font-size: 15px; margin-top: 4px; }

  .card--details .brand-lockup {
    left: auto; right: 80px; top: 118px;
    color: var(--brand-blue);
  }
  .rule {
    position: absolute; height: 0;
    border-top: 1.5px solid var(--rule);
  }
  .rule--upper { left: 80px; right: 80px; top: 200px; }
  .rule--lower { left: 60px; right: 60px; top: 370px; }
  .rule--dashed { left: 40px; right: 40px; top: 440px; border-top: 1.5px dashed var(--dash); }

  .contact-list {
    position: absolute; top: 228px;
    list-style: none;
    display: flex; flex-direction: column; gap: 16px;
    font-size: 19px;
  }
  .contact-list--direct { left: 90px; }
  .contact-list--social { left: 520px; }
  .contact-list li { display: flex; align-items: center; gap: 14px; }
  .contact-icon { width: 26px; height: 26px; flex: none; }
  .social-dot { width: 26px; height: 26px; border-radius: 50%; flex: none; }
  .social-dot--a { background: var(--social-a); }
  .social-dot--b { background: var(--social-b); }
</style>
</head>
<body>

  <section class="card card--brand" aria-label="Business card, brand side">
    <div class="brand-disc" role="img" aria-label="Clinic emblem area"></div>
    <div class="brand-lockup">
      <span class="lockup-dot"></span>
      <span class="lockup-name">
        <span class="line-1">The Harbourview</span>
        <span class="line-2">Motion Clinic</span>
      </span>
    </div>
  </section>

  <section class="card card--details" aria-label="Business card, contact side">
    <div class="person">
      <p class="person-name">Name of <span class="accent">Person</span></p>
      <p class="person-role">Designation</p>
    </div>

    <div class="brand-lockup">
      <span class="lockup-dot"></span>
      <span class="lockup-name">
        <span class="line-1">The Harbourview</span>
        <span class="line-2">Motion Clinic</span>
      </span>
    </div>

    <div class="rule rule--upper"></div>

    <ul class="contact-list contact-list--direct">
      <li>
        <svg class="contact-icon" viewBox="0 0 24 24" aria-hidden="true">
          <circle cx="12" cy="12" r="10.5" fill="none" stroke="#1b1b1b" stroke-width="1.8"/>
          <path d="M9.2 7.2c.5-.4 1.1-.3 1.3.2l.8 1.8c.2.4 0 .8-.3 1.1l-.6.5c.5 1.2 1.4 2.2 2.6 2.8l.5-.6c.3-.3.8-.4 1.1-.2l1.7.9c.5.2.6.9.2 1.3l-.8.8c-.6.6-1.6.7-2.5.2-2.4-1.3-4.2-3.3-5.1-5.8-.3-.9-.1-1.8.5-2.4z" fill="#1b1b1b"/>
        </svg>
        <span>555.014.2290</span>
      </li>
      <li>
        <svg class="contact-icon" viewBox="0 0 24 24" aria-hidden="true">
          <rect x="2" y="5" width="20" height="14" fill="#1b1b1b"/>
          <path d="M2 5l10 8 10-8" fill="none" stroke="#fbfbfb" stroke-width="1.6"/>
        </svg>
        <span>hello@harbourviewmotion.com</span>
      </li>
    </ul>

    <ul class="contact-list contact-list--social">
      <li><span class="social-dot social-dot--a"></span><span>social/name</span></li>
      <li><span class="social-dot social-dot--b"></span><span>gallery_name</span></li>
    </ul>

    <div class="rule rule--lower"></div>
    <div class="rule rule--dashed"></div>
  </section>

</body>
</html>
```